executive development which breaks down traditional practices and thought processes

4 or 5 page website. Home page idea is fixed but needs creative execution to work {see attachment}, branding, as in corporate identity is in place and ready to go, (see attachment). Site needs to reflect the the market and typical participant, which are very high achievers up to and including Board Level Members in 'world leading company's'.

What we do is different, we are often copied, but without the success.

We require simple, slick impact, we have powerful messages that need to be supported by exquisite, simplistic design. We know we are the best out there and have kept our heads under water, but now is the time to start our expansion process.

We have copywriters briefed, and are liking what we read, so time to engage with designers who might like to 'wow' us, as well as our existing and potential clients.

Pages to include a standard landing/home page, about us, methodology, testimonials/awards and let's talk pages. Our philosophy is: opening minds to new ways of thinking, being, working and acting; to challenge long held business, management and leadership biases.

Our experiential learning technique is branded 'Tamarind' where we take people out of their comfort zone or into new & very different environments; to experience the way methodology and leadership techniques from uncomfortable encounters can be beneficial in big business strategic decision making, being more innovative and solving leadership & managerial challenges with new eyes (or a new perspective).

We will need to include video clips for awards we have won and testimonials from participants and company's alike. We work across the globe, the site needs to reflect this, without us looking like a huge corporate company, which we are not. We are small but pack a powerful punch, and that's the way we like it. Our clients don't see us as consultants or suppliers, more as the missing cog or the oil in the machine to get their executives to engage and deliver unorthodox thought processes which keep them at the forefront of their industries.

Both the copywriters and ourselves see typography being a crucial element to the impact of the site, so those designers with a passion in this area may well find our preference.

We are ready to go, good luck.

sorry guys missing the brief by a long way, we always said we were not looking for an off the shelf solution/concept which could be created on any 'sun pebble' like ortal and to be honest that's all we have received

Reason: designs miss the brief

Reason: We are not getting the desired simplistic landing page required.

```html
<!DOCTYPE html>
<html lang="en">
<head>
<meta charset="utf-8">
<title>Northway Executive development</title>
<link rel="stylesheet" href="https://fonts.googleapis.com/css2?family=Open+Sans:wght@600;700&family=Oxygen:wght@400;700&display=swap">
<style>
  :root {
    --photo-light: #dfe8ef;
    --photo-mid: #a9bfd0;
    --photo-dark: #7f9ab0;
    --brand-green: #3fd21a;
    --accent-purple: #3b10f0;
    --accent-green: #44ff00;
    --pill-grey: #676767;
    --card-top: #ececec;
    --card-bottom: #f6f6f6;
    --ink: #333333;
    --footer-grey: #666666;
    --white: #ffffff;
  }
  * { box-sizing: border-box; margin: 0; padding: 0; }
  html, body { width: 1200px; height: 765px; overflow: hidden; }
  body {
    position: relative;
    font-family: "Oxygen", Arial, sans-serif;
    color: var(--ink);
  }
  .hero-photo {
    position: absolute; left: 0; top: 0; width: 1200px; height: 684px;
    background:
      radial-gradient(ellipse 300px 200px at 600px 390px, #f3f6f8 0%, rgba(243,246,248,0) 100%),
      radial-gradient(ellipse 420px 360px at 960px 220px, #e8d6cc 0%, rgba(232,214,204,0) 70%),
      linear-gradient(160deg, var(--photo-light) 0%, var(--photo-mid) 55%, var(--photo-dark) 100%);
  }
  .brand {
    position: absolute; left: 420px; top: 26px; width: 360px;
    text-align: center;
  }
  .brand-name {
    font-family: "Open Sans", Arial, sans-serif; font-weight: 700;
    font-size: 76px; line-height: 1; color: var(--brand-green);
    letter-spacing: -1px;
  }
  .brand-tagline {
    margin-top: 10px; font-family: "Open Sans", Arial, sans-serif; font-weight: 600;
    font-size: 20px; color: #6a6a6a; text-align: right; padding-right: 4px;
  }
  .section-pill {
    position: absolute; height: 33px;
    background: var(--pill-grey); color: var(--white);
    font-family: "Open Sans", Arial, sans-serif; font-weight: 600; font-size: 21px;
    line-height: 33px; text-align: center;
    box-shadow: 0 3px 5px rgba(0,0,0,0.25);
  }
  .pill-noun { left: 517px; top: 172px; width: 165px; }
  .pill-verb { left: 517px; top: 437px; width: 188px; }
  .sense-card {
    position: absolute; width: 168px; height: 156px;
    background: linear-gradient(180deg, var(--card-top), var(--card-bottom));
    border-radius: 3px;
    box-shadow: 0 1px 3px rgba(0,0,0,0.25);
  }
  .sense-head {
    position: relative; height: 21px; margin-top: 0;
    background: linear-gradient(90deg, var(--accent-purple) 0%, #3b3fd0 45%, #35b84a 80%, var(--accent-green) 100%);
    border-top: 2px solid #f6f6f6;
    color: var(--white); font-family: "Open Sans", Arial, sans-serif; font-weight: 600;
    font-size: 19px; line-height: 19px; text-align: center;
  }
  .sense-head svg { position: absolute; left: 0; top: -10px; }
  .sense-body {
    padding: 9px 10px 0 11px; font-size: 12.3px; line-height: 18px;
    text-transform: capitalize; letter-spacing: 0.1px;
  }
  .sub-sense { display: flex; align-items: flex-start; margin-top: 14px; }
  .sub-sense svg { flex: none; margin-right: 6px; margin-top: 0; }
  .site-footer {
    position: absolute; left: 0; top: 684px; width: 1200px; height: 81px;
    background: var(--footer-grey); border-top: 4px solid var(--accent-green);
    color: var(--white); font-family: "Open Sans", Arial, sans-serif; font-weight: 600;
    text-align: center;
  }
  .footer-nav { margin-top: 14px; font-size: 16px; }
  .footer-nav a { color: var(--white); text-decoration: none; }
  .footer-nav .sep { margin: 0 8px; }
  .copyright { margin-top: 11px; font-size: 16px; }
</style>
</head>
<body>
  <div class="hero-photo" role="img" aria-label="Photograph of a hand placing the last piece into a pale blue jigsaw puzzle"></div>

  <header class="brand">
    <div class="brand-name">Northway</div>
    <div class="brand-tagline">Executive development</div>
  </header>

  <div class="section-pill pill-noun">quest (kwest)</div>

  <svg width="0" height="0" style="position:absolute">
    <defs>
      <symbol id="leaf" viewBox="0 0 44 30">
        <path d="M2 29 C2 14 14 2 30 2 L43 2 C43 18 30 29 14 29 Z" fill="#4a10f5" stroke="#2a0a90" stroke-width="1.5"/>
      </symbol>
      <symbol id="tag" viewBox="0 0 26 20">
        <path d="M10 1 H18 L25 10 L18 19 H10 A9 9 0 0 1 10 1 Z" fill="#4a2fd8"/>
      </symbol>
    </defs>
  </svg>

  <article class="sense-card" style="left:234px; top:233px;">
    <div class="sense-head"><svg width="43" height="29"><use href="#leaf"/></svg>1</div>
    <p class="sense-body">The act or an instance of looking for or seeking; search: a quest for diamonds.</p>
  </article>
  <article class="sense-card" style="left:422px; top:233px;">
    <div class="sense-head"><svg width="43" height="29"><use href="#leaf"/></svg>2</div>
    <p class="sense-body">(Historical terms) (in medieval romance) an expedition by a knight or company of knights to accomplish some prescribed task, such as finding the Holy Grail</p>
  </article>
  <article class="sense-card" style="left:609px; top:233px;">
    <div class="sense-head"><svg width="43" height="29"><use href="#leaf"/></svg>3</div>
    <p class="sense-body">The object of a search; goal or target: my quest is the treasure of the king.</p>
  </article>
  <article class="sense-card" style="left:797px; top:233px;">
    <div class="sense-head"><svg width="43" height="29"><use href="#leaf"/></svg>4</div>
    <p class="sense-body">A collection of alms</p>
  </article>

  <div class="section-pill pill-verb">vb (mainly intr)</div>

  <article class="sense-card" style="left:140px; top:498px;">
    <div class="sense-head"><svg width="43" height="29"><use href="#leaf"/></svg>5</div>
    <p class="sense-body">(foll by: for or after) to go in search (of)</p>
  </article>
  <article class="sense-card" style="left:327px; top:498px;">
    <div class="sense-head"><svg width="43" height="29"><use href="#leaf"/></svg>6</div>
    <p class="sense-body">(Historical terms) to go on a quest</p>
  </article>
  <article class="sense-card" style="left:516px; top:498px;">
    <div class="sense-head"><svg width="43" height="29"><use href="#leaf"/></svg>7</div>
    <div class="sense-body">
      <p>(Hunting) (of gun dogs or hounds)</p>
      <p class="sub-sense"><svg width="24" height="19"><use href="#tag"/><text x="11" y="14" fill="#fff" font-size="13" font-weight="700" text-anchor="middle" font-family="Oxygen, Arial, sans-serif">a</text></svg><span>To search for game</span></p>
      <p class="sub-sense"><svg width="24" height="19"><use href="#tag"/><text x="11" y="14" fill="#fff" font-size="13" font-weight="700" text-anchor="middle" font-family="Oxygen, Arial, sans-serif">b</text></svg><span>To bay when in pursuit of game</span></p>
    </div>
  </article>
  <article class="sense-card" style="left:703px; top:498px;">
    <div class="sense-head"><svg width="43" height="29"><use href="#leaf"/></svg>8</div>
    <p class="sense-body">To collect alms</p>
  </article>
  <article class="sense-card" style="left:892px; top:498px;">
    <div class="sense-head"><svg width="43" height="29"><use href="#leaf"/></svg>9</div>
    <p class="sense-body">(also tr) to go in search of (a thing); seek or pursue</p>
  </article>

  <footer class="site-footer">
    <nav class="footer-nav">
      <a href="#">Home</a><span class="sep">|</span><a href="#">About Us</a><span class="sep">|</span><a href="#">Methodology</a><span class="sep">|</span><a href="#">Testimonials/awards</a><span class="sep">|</span><a href="#">Let's Talk</a>
    </nav>
    <p class="copyright">© 2014 Northway Executive development. All right reserved.</p>
  </footer>
</body>
</html>
```